Template Flyer- Corewell Stretch & Flow

I am wanting a template 1 page flyer designed to use on the back ground of newsletter (faded background) and for our advertising posters in A4, A3, for Facebook and Instagram compatibility.

I have loaded an example from another Studio called Pinegrove (file 3)- each time they have a new workshop to advertise a picture is placed in the little circle (so this is something I would want to do too where I can load a new picture each time a new workshop is running)- They have used the flyer like a water mark...I like this.

Our colour palette is what is on our logos and you can also visit our website for a feel for what we like www.corewellstretch.com.au

I need some of the designs edited a bit more and because of the time difference, there seems to be a 24hour period where we communicate with each other. May I please request another 2 days extension

Requirements
Must have
• Id like to have a picture in the back ground. My favourite back ground that has been produced so far is a background of both picture file 9 and 10 in either.
Nice to have
• 3 picture circles options to advertise the events/workshops I have each year.
• Brush stroke style circles (see picture attached)rather then smooth circles for the picture area (in a grey tone)
Should not have
• No BLACK colour writing or black circles

```html
<!DOCTYPE html>
<html lang="en">
<head>
<meta charset="utf-8">
<title>Corewell Stretch &amp; Flow – One Day Retreat</title>
<link href="https://fonts.googleapis.com/css2?family=Jost:ital,wght@0,400;0,500;0,600;0,700;1,600&family=Poppins:wght@700&display=swap" rel="stylesheet">
<style>
  :root {
    --teal: #1a89a6;
    --slate: #55575a;
    --ink: #4a4c50;
    --stone: #a9a49e;
    --paper: #f4f2ef;
    --pill: #565759;
    --white: #ffffff;
  }
  * { box-sizing: border-box; margin: 0; padding: 0; }
  html, body { width: 960px; height: 1200px; overflow: hidden; }
  body { font-family: "Jost", sans-serif; color: var(--ink); }

  .flyer { position: relative; width: 960px; height: 1200px; overflow: hidden; background: var(--paper); }

  .backdrop {
    position: absolute; inset: 0;
    background:
      radial-gradient(ellipse at 88% 92%, rgba(200,214,200,.55) 0, rgba(200,214,200,0) 30%),
      radial-gradient(ellipse at 10% 40%, rgba(226,218,204,.6) 0, rgba(226,218,204,0) 45%),
      linear-gradient(180deg, #f6f5f3 0%, #f0eeeb 60%, #ebe9e5 100%);
  }
  .backdrop-ring {
    position: absolute; left: 60px; top: -20px; width: 860px; height: 1250px;
    border: 6px solid rgba(190,188,184,.35); border-radius: 50%;
  }

  .brand { position: absolute; top: 68px; left: 0; width: 960px; text-align: center; }
  .brand-name { display: inline-flex; align-items: center; gap: 14px; font-size: 48px; font-weight: 500; color: var(--teal); letter-spacing: .5px; }
  .brand-dot { width: 22px; height: 22px; border-radius: 50%; background: var(--teal); }

  .feature-art { position: absolute; left: 0; top: 0; }

  .feature-title {
    position: absolute; top: 292px; left: 240px; width: 470px; text-align: center;
    font-family: "Poppins", sans-serif; font-weight: 700; font-size: 66px; line-height: .98;
    color: var(--white); letter-spacing: -1px;
  }

  .event-heading { position: absolute; top: 752px; width: 960px; text-align: center; font-size: 32px; font-weight: 600; color: var(--teal); }

  .details {
    position: absolute; top: 814px; left: 96px; width: 768px; height: 82px;
    border: 1.5px solid #8f8f8f; border-radius: 40px; display: flex;
  }
  .details-col { padding: 10px 0 0 24px; font-size: 24px; font-weight: 600; color: var(--slate); line-height: 1.4; }
  .details-col + .details-col { border-left: 1.5px solid #b5b5b5; padding-left: 30px; }
  .details-col:first-child { width: 325px; }
  .accent { color: var(--teal); }

  .facilitators { position: absolute; top: 923px; width: 960px; text-align: center; }
  .facilitators-label { display: flex; align-items: center; justify-content: center; gap: 14px; font-size: 29px; font-weight: 600; font-style: italic; color: var(--teal); }
  .facilitators-label::before, .facilitators-label::after { content: ""; width: 285px; height: 1.5px; background: var(--teal); opacity: .7; }
  .facilitators-names { margin-top: 2px; font-size: 22px; font-weight: 600; color: var(--slate); }
  .facilitators-blurb { margin: 2px auto 0; width: 850px; font-size: 22px; line-height: 1.25; color: var(--slate); }

  .web { position: absolute; top: 1086px; left: 0; width: 960px; display: flex; align-items: center; justify-content: center; gap: 10px; }
  .web::before, .web::after { content: ""; width: 130px; height: 2px; background: var(--slate); }
  .web-pill { width: 576px; height: 52px; border-radius: 14px; background: var(--pill); color: var(--white); font-size: 31px; font-weight: 500; text-align: center; line-height: 52px; }

  .contact { position: absolute; top: 1150px; width: 960px; display: flex; justify-content: center; align-items: center; font-size: 18px; color: var(--slate); }
  .contact-item { display: flex; align-items: center; gap: 8px; padding: 0 14px; }
  .contact-item + .contact-item { border-left: 1.5px solid #9a9a9a; }
  .contact-item svg { width: 22px; height: 22px; }
</style>
</head>
<body>
<main class="flyer">
  <div class="backdrop" role="img" aria-label="Faded photo of a pilates studio with a pilates ring and patterned bolsters"></div>
  <div class="backdrop-ring"></div>

  <header class="brand">
    <div class="brand-name"><span class="brand-dot"></span>Corewell Stretch &amp; Flow</div>
  </header>

  <svg class="feature-art" width="960" height="760" viewBox="0 0 960 760">
    <defs>
      <linearGradient id="tassels" x1="0" y1="0" x2="1" y2="1">
        <stop offset="0" stop-color="#b5895a"/>
        <stop offset=".45" stop-color="#e7e2d8"/>
        <stop offset=".7" stop-color="#c98a4a"/>
        <stop offset="1" stop-color="#8e5b34"/>
      </linearGradient>
      <linearGradient id="bolsters" x1="0" y1="0" x2="1" y2="1">
        <stop offset="0" stop-color="#b9d6dc"/>
        <stop offset=".5" stop-color="#d9e3b8"/>
        <stop offset="1" stop-color="#9fc2cf"/>
      </linearGradient>
      <linearGradient id="studio" x1="0" y1="0" x2="0" y2="1">
        <stop offset="0" stop-color="#f1f1ef"/>
        <stop offset=".6" stop-color="#d8d8d6"/>
        <stop offset="1" stop-color="#9a9c9e"/>
      </linearGradient>
    </defs>
    <circle cx="475" cy="420" r="242" fill="url(#tassels)" role="img" aria-label="Photo of beaded tassels hanging in a studio doorway"/>
    <circle cx="475" cy="420" r="250" fill="none" stroke="var(--stone)" stroke-width="14" opacity=".9"/>
    <circle cx="697" cy="482" r="104" fill="url(#bolsters)" role="img" aria-label="Photo of a pile of patterned meditation bolsters"/>
    <circle cx="697" cy="482" r="106" fill="none" stroke="#8d8d8d" stroke-width="5"/>
    <circle cx="616" cy="628" r="86" fill="url(#studio)" role="img" aria-label="Photo of a studio floor set with mats and cushions"/>
    <circle cx="616" cy="628" r="88" fill="none" stroke="#8d8d8d" stroke-width="5"/>
  </svg>

  <h1 class="feature-title">ONE DAY<br>RETREAT</h1>

  <h2 class="event-heading">1 Day Retreat (Lunch included)</h2>

  <section class="details">
    <div class="details-col">Saturday 24th March<br><span class="accent">10.000m - 4.00pm</span></div>
    <div class="details-col">Cost: $120 per person<br><span class="accent">$100</span> Concession card holders</div>
  </section>

  <section class="facilitators">
    <div class="facilitators-label">Facilitated by</div>
    <div class="facilitators-names">Mira Hallett, Jo Penrose, Tess Arland</div>
    <p class="facilitators-blurb">A weekend full of Inspiration, guided meditation, Yoga, Pilates, relaxation, philosophy, yummy nutritious Food, and empowering information to live well in the world.</p>
  </section>

  <div class="web"><div class="web-pill">www.corewellstretchandflow.com</div></div>

  <footer class="contact">
    <div class="contact-item">
      <svg viewBox="0 0 24 24"><circle cx="12" cy="12" r="11" fill="none" stroke="var(--teal)" stroke-width="1.5"/><path d="M12 5a4.5 4.5 0 0 0-4.5 4.5c0 3.4 4.5 8.5 4.5 8.5s4.5-5.1 4.5-8.5A4.5 4.5 0 0 0 12 5z" fill="var(--teal)"/><circle cx="12" cy="9.5" r="1.7" fill="#fff"/></svg>
      18 Harlow Street, Ashbury, VIC 3999
    </div>
    <div class="contact-item">
      <svg viewBox="0 0 24 24"><circle cx="12" cy="12" r="11" fill="none" stroke="var(--teal)" stroke-width="1.5"/><path d="M8 6.5l2 0 1 3-1.4 1a7 7 0 0 0 3.9 3.9l1-1.4 3 1v2a1.5 1.5 0 0 1-1.6 1.5A10 10 0 0 1 6.5 8.1 1.5 1.5 0 0 1 8 6.5z" fill="var(--teal)"/></svg>
      (03) 5550 0142
    </div>
    <div class="contact-item">
      <svg viewBox="0 0 24 24"><circle cx="12" cy="12" r="11" fill="none" stroke="var(--teal)" stroke-width="1.5"/><rect x="6" y="8" width="12" height="8.5" rx="1" fill="var(--teal)"/><path d="M6.5 8.5l5.5 4.2 5.5-4.2" fill="none" stroke="#fff" stroke-width="1.2"/></svg>
      info@corewellstretchandflow.com
    </div>
  </footer>
</main>
</body>
</html>
```